The Linen Loft Co

We need a business card design for our wardrobe company.
Please visit our website www.gentlelinenlofts.com to get an idea of who we are.

```html
<!DOCTYPE html>
<html lang="en">
<head>
<meta charset="utf-8">
<title>The Linen Loft Co – Business Card</title>
<link rel="stylesheet" href="https://fonts.googleapis.com/css2?family=Arimo:wght@400;700&family=Lato:wght@400&family=Montserrat:wght@500&display=swap">
<style>
  :root {
    --backdrop: #e6e6e6;
    --card: #ffffff;
    --ink: #111111;
    --gold: #8c7451;
    --rule: #b9a47f;
    --grey-text: #444444;
    --contact-text: #3a3a3a;
  }
  html, body {
    margin: 0;
    padding: 0;
    width: 1200px;
    height: 1200px;
    overflow: hidden;
    background: var(--backdrop);
  }
  .card {
    position: absolute;
    left: 65px;
    top: 288px;
    width: 1070px;
    height: 625px;
    background: var(--card);
    border-radius: 48px;
  }
  .brand-mark {
    position: absolute;
    left: 291px;
    top: 89px;
    width: 130px;
    height: 130px;
    background: var(--gold);
  }
  .brand-name {
    position: absolute;
    left: 442px;
    top: 102px;
    margin: 0;
    font-family: "Montserrat", sans-serif;
    font-weight: 500;
    font-size: 33px;
    line-height: 42px;
    letter-spacing: 0.5px;
    color: var(--ink);
    text-transform: uppercase;
    white-space: nowrap;
  }
  .tagline {
    position: absolute;
    left: 485px;
    top: 160px;
    margin: 0;
    font-family: "Arimo", sans-serif;
    font-weight: 400;
    font-size: 30px;
    line-height: 40px;
    color: var(--ink);
    white-space: nowrap;
  }
  .person {
    position: absolute;
    left: 0;
    right: 0;
    text-align: center;
    font-family: "Arimo", sans-serif;
  }
  .person-name {
    top: 314px;
    margin: 0;
    font-weight: 700;
    font-size: 40px;
    line-height: 48px;
    color: var(--gold);
  }
  .person-role {
    top: 368px;
    margin: 0;
    font-weight: 400;
    font-size: 32px;
    line-height: 40px;
    color: var(--grey-text);
  }
  .divider {
    position: absolute;
    left: 42px;
    width: 992px;
    top: 434px;
    height: 2px;
    background: var(--rule);
  }
  .contacts {
    position: absolute;
    left: 43px;
    top: 454px;
    margin: 0;
    padding: 0;
    list-style: none;
    font-family: "Lato", sans-serif;
    font-size: 25px;
    line-height: 33px;
    color: var(--contact-text);
  }
  .contacts li {
    display: flex;
    align-items: center;
    height: 33px;
  }
  .contacts svg {
    width: 16px;
    height: 16px;
    margin-right: 11px;
    flex: none;
  }
  .address {
    position: absolute;
    right: 38px;
    top: 491px;
    margin: 0;
    text-align: right;
    font-family: "Lato", sans-serif;
    font-style: normal;
    font-size: 25px;
    line-height: 32px;
    letter-spacing: 0.5px;
    color: var(--contact-text);
  }
</style>
</head>
<body>
  <div class="card">
    <div class="brand-mark"></div>
    <p class="brand-name">The Linen Loft Co</p>
    <p class="tagline">Keeping it Tidy and Calm</p>

    <p class="person person-name">Dara Whitlock</p>
    <p class="person person-role">Manager</p>

    <div class="divider"></div>

    <ul class="contacts">
      <li>
        <svg viewBox="0 0 16 16" aria-hidden="true"><path d="M3.5 1.5l2.5 0.5 1 3-1.7 1.2a9 9 0 0 0 4.5 4.5L11 9l3 1 .5 2.5-2 2C7 14 2 9 1.5 3.5z" fill="var(--gold)"/></svg>
        403-555-0142
      </li>
      <li>
        <svg viewBox="0 0 16 16" aria-hidden="true"><rect x="4" y="1" width="8" height="14" rx="1.5" fill="none" stroke="var(--gold)" stroke-width="1.6"/><circle cx="8" cy="12.5" r="0.9" fill="var(--gold)"/></svg>
        403-555-0187
      </li>
      <li>
        <svg viewBox="0 0 16 16" aria-hidden="true"><rect x="1" y="3" width="14" height="10" fill="var(--gold)"/><path d="M1.5 3.5L8 9l6.5-5.5" fill="none" stroke="#fff" stroke-width="1.3"/></svg>
        info@gentlelinenlofts.com
      </li>
      <li>
        <svg viewBox="0 0 16 16" aria-hidden="true"><circle cx="8" cy="8" r="6.5" fill="var(--gold)"/><path d="M1.5 8h13M8 1.5c-2.5 3-2.5 10 0 13M8 1.5c2.5 3 2.5 10 0 13" fill="none" stroke="#fff" stroke-width="1"/></svg>
        www.gentlelinenlofts.com
      </li>
    </ul>

    <address class="address">
      18-20 Marlow<br>
      Bend Avenue<br>
      552190, USA
    </address>
  </div>
</body>
</html>
```